Coastline Premier Retreats Business Card Design

Design a business card for Coastline Premier Retreats. Look at the website for colors and reference. Card should have logo, name, title, office number, mobile number, email, URL and a tagline like, "Luxury Hotel & Resort Email Marketing" (This might change).

https://www.coastlinepremierretreats.example

The rest I will leave up to your imagination.

Contact Information for Business Card

Logo, name, title, office number, mobile number, email, URL and a tagline like, "Luxury Hotel & Resort Email Marketing" (This might change).

```html
<!DOCTYPE html>
<html lang="en">
<head>
<meta charset="utf-8">
<title>Coastline Premier Retreats – Business Card</title>
<link rel="stylesheet" href="https://fonts.googleapis.com/css2?family=Montserrat:wght@400;500;700;800&display=swap">
<style>
  :root {
    --stage: #2b2b2b;
    --card: #1a1a1a;
    --accent: #f07a12;
    --ink: #ffffff;
    --shadow: rgba(0, 0, 0, 0.55);
  }
  * { box-sizing: border-box; margin: 0; padding: 0; }
  html, body { width: 1200px; height: 900px; overflow: hidden; }
  body {
    background: var(--stage);
    font-family: "Montserrat", Arial, sans-serif;
    color: var(--ink);
    position: relative;
  }
  .card {
    position: absolute;
    left: 250px;
    width: 700px;
    height: 400px;
    background: var(--card);
    border-left: 4px solid var(--accent);
    border-bottom: 4px solid var(--accent);
    box-shadow: 0 14px 30px var(--shadow);
  }
  .card--front { top: 36px; }
  .card--back { top: 464px; }

  /* Front */
  .brand {
    position: absolute;
    left: 0; right: 0; top: 130px;
    text-align: center;
  }
  .brand__name {
    font-weight: 800;
    font-size: 40px;
    letter-spacing: 1px;
    text-transform: uppercase;
    color: var(--ink);
    display: inline-flex;
    align-items: center;
    gap: 16px;
  }
  .brand__mark {
    width: 22px; height: 22px;
    background: var(--accent);
    display: inline-block;
  }
  .tagline {
    position: absolute;
    left: 0; right: 0; top: 300px;
    text-align: center;
    color: var(--accent);
    font-size: 20px;
    font-weight: 500;
    letter-spacing: 0.5px;
  }

  /* Back */
  .person {
    position: absolute;
    right: 390px;
    top: 132px;
    text-align: right;
  }
  .person__name {
    color: var(--accent);
    font-weight: 800;
    font-size: 34px;
    letter-spacing: 1px;
    text-transform: uppercase;
    line-height: 1;
  }
  .person__title {
    font-size: 17px;
    font-weight: 400;
    margin-top: 6px;
  }
  .divider {
    position: absolute;
    left: 330px;
    top: 100px;
    width: 1.5px;
    height: 120px;
    background: var(--accent);
  }
  .contacts {
    position: absolute;
    left: 352px;
    top: 98px;
    list-style: none;
    font-size: 15px;
    font-weight: 400;
    line-height: 1;
  }
  .contacts li {
    display: flex;
    align-items: center;
    gap: 9px;
    height: 31px;
  }
  .contacts svg { width: 14px; height: 14px; fill: var(--accent); flex: none; }
  .contacts .domain { color: var(--accent); }
  .address {
    position: absolute;
    left: 0; right: 0;
    bottom: 52px;
    text-align: center;
    font-size: 17px;
    letter-spacing: 0.3px;
  }
</style>
</head>
<body>

<section class="card card--front" aria-label="Card front">
  <div class="brand">
    <span class="brand__name"><span class="brand__mark"></span>Coastline Premier Retreats</span>
  </div>
  <p class="tagline">Luxury Hotel &amp; Resort Email Marketing</p>
</section>

<section class="card card--back" aria-label="Card back">
  <div class="person">
    <p class="person__name">Daniel Moreau</p>
    <p class="person__title">CEO/Founder</p>
  </div>
  <span class="divider"></span>
  <ul class="contacts">
    <li>
      <svg viewBox="0 0 16 16" aria-hidden="true"><path d="M4 1h8a1 1 0 0 1 1 1v12a1 1 0 0 1-1 1H4a1 1 0 0 1-1-1V2a1 1 0 0 1 1-1zm1 2v9h6V3zm3 10a.8.8 0 1 0 0 .01z"/></svg>
      555.014.2270
    </li>
    <li>
      <svg viewBox="0 0 16 16" aria-hidden="true"><path d="M1 6c0-2 3-3 7-3s7 1 7 3v1h-4V5.5H5V7H1zm3 2h8l2 6H2z"/></svg>
      +34 600 000 147
    </li>
    <li>
      <svg viewBox="0 0 16 16" aria-hidden="true"><path d="M1 4h14v9H1zm1.5 1.2L8 9.3l5.5-4.1z"/></svg>
      info@coastlinepremierretreats.example
    </li>
    <li>
      <svg viewBox="0 0 16 16" aria-hidden="true"><path d="M8 1a7 7 0 1 0 .01 0zm0 1.5c.9 1 1.5 2.6 1.7 4.5H6.3C6.5 5.1 7.1 3.5 8 2.5zM2.6 7.8h2.9c.1 1.9.7 3.6 1.5 4.8a5.5 5.5 0 0 1-4.4-4.8zm5.4 5c-.9-1-1.5-2.9-1.7-5h3.4c-.2 2.1-.8 4-1.7 5zm1-.2c.8-1.2 1.4-2.9 1.5-4.8h2.9a5.5 5.5 0 0 1-4.4 4.8z"/></svg>
      <span>www.<span class="domain">coastlinepremierretreats</span>.example</span>
    </li>
  </ul>
  <p class="address">Po Box, 48 B Harbor Rd North America, AB 40210</p>
</section>

</body>
</html>
```